Business Card Re-Design/Update

We'd like to update out business cards. I've included our current "Style guide" which has the colour scheme of the organisation in it. I've also included the branding files with logos etc in them.

I've also included a copy of one of our existing cards so that you can see how ugly/dated they look. I'd like a fresh modern corporate look.

Target Market(s)

These are for our clients, potential clients, industry contacts - like all business cards

Contact Information for Business Card

Name
Position
Company Address - Level 1, 47 Fernby Street, Carlow Qld 4072
Direct Phone
mobile
Email
Website -www.korvalit.com.au
Logo

Colors

Designer to choose colors to be used in the design.

Requirements
Must have
• Main Logo
• Cards will need to be editable to be able to personalize them for each new employee.
Nice to have
• The MapOut, ShipWell, KeepSteady would be okay to have if they can be sensibly and professionally added to the look without detracting from the main imagery.
• Maybe they could go on the back of the card? will leave this to your creative discretion as to whether/where they fit.
Should not have
• Should not have decorative or script fonts

```html
<!DOCTYPE html>
<html lang="en">
<head>
<meta charset="utf-8">
<title>Korval business card</title>
<link href="https://fonts.googleapis.com/css2?family=Roboto:wght@400;500;700&family=Roboto+Condensed:wght@400;500&display=swap" rel="stylesheet">
<style>
  :root {
    --backdrop: #2b2b2b;
    --paper: #f2f2f2;
    --ink: #231f20;
    --text: #4a4a4a;
    --red: #c8161d;
    --red-dark: #a50f15;
    --red-light: #d81e25;
    --white: #ffffff;
  }
  html, body {
    margin: 0;
    padding: 0;
    width: 1200px;
    height: 960px;
    overflow: hidden;
    background: var(--backdrop);
    font-family: "Roboto", Arial, sans-serif;
  }
  .canvas {
    position: relative;
    width: 1200px;
    height: 960px;
  }
  .card {
    position: absolute;
    width: 600px;
    height: 342px;
    overflow: hidden;
  }
  /* Front */
  .card-front {
    left: 322px;
    top: 108px;
    background: var(--paper);
  }
  .brand {
    position: absolute;
    left: 34px;
    top: 46px;
    display: flex;
    align-items: center;
    gap: 14px;
  }
  .brand-mark {
    width: 36px;
    height: 36px;
    background: var(--red);
  }
  .brand-name {
    font-family: "Roboto", Arial, sans-serif;
    font-weight: 500;
    font-size: 38px;
    line-height: 1;
    color: var(--ink);
  }
  .address {
    position: absolute;
    left: 33px;
    top: 152px;
    margin: 0;
    font-size: 14px;
    line-height: 18px;
    color: var(--text);
    font-style: normal;
  }
  .contacts {
    position: absolute;
    left: 33px;
    top: 196px;
    margin: 0;
    padding: 0;
    list-style: none;
    font-size: 14px;
    line-height: 19px;
    color: var(--text);
  }
  .contacts li {
    display: flex;
    align-items: center;
    gap: 8px;
  }
  .contacts svg {
    width: 14px;
    height: 14px;
    flex: none;
    fill: var(--red);
  }
  .name-band {
    position: absolute;
    right: 0;
    top: 199px;
    width: 242px;
    height: 63px;
    background: linear-gradient(180deg, var(--red-light), var(--red-dark));
    color: var(--white);
    text-align: right;
    box-sizing: border-box;
    padding: 10px 25px 0 0;
    font-family: "Roboto Condensed", Arial, sans-serif;
  }
  .name-tab {
    position: absolute;
    left: 350px;
    top: 190px;
    width: 8px;
    height: 80px;
    background: var(--red-dark);
  }
  .person-name {
    margin: 0;
    font-size: 21px;
    font-weight: 500;
    line-height: 24px;
    letter-spacing: 0.2px;
  }
  .person-role {
    margin: 0;
    font-size: 15px;
    line-height: 18px;
  }
  /* Back */
  .card-back {
    left: 320px;
    top: 493px;
    background: radial-gradient(ellipse at 48% 45%, #dc1f26 0%, var(--red) 55%, #b31118 100%);
  }
  .back-name {
    position: absolute;
    left: 0;
    right: 0;
    top: 114px;
    text-align: center;
    font-weight: 500;
    font-size: 64px;
    line-height: 1;
    color: var(--white);
  }
  .services {
    position: absolute;
    left: 46px;
    right: 40px;
    top: 274px;
    display: flex;
    justify-content: space-between;
    margin: 0;
    padding: 0;
    list-style: none;
  }
  .service {
    display: flex;
    align-items: center;
    gap: 8px;
    font-weight: 500;
    font-size: 27px;
    line-height: 1;
    color: var(--white);
    letter-spacing: -0.5px;
  }
  .service-mark {
    width: 22px;
    height: 22px;
    background: var(--white);
  }
</style>
</head>
<body>
<main class="canvas">

  <section class="card card-front" aria-label="Business card front">
    <div class="brand">
      <span class="brand-mark"></span>
      <span class="brand-name">Korval</span>
    </div>

    <address class="address">
      Level 1, 47 Fernby Street<br>
      Carlow Qld 4072
    </address>

    <ul class="contacts">
      <li>
        <svg viewBox="0 0 16 16" aria-hidden="true"><path d="M3.5 1l3 3-1.6 1.8c.8 2 2.3 3.5 4.3 4.3L11 8.5l3 3-2 2.5C6.5 14 2 9.5 1 3.5z"/></svg>
        +61 (0)7 5550 1482
      </li>
      <li>
        <svg viewBox="0 0 16 16" aria-hidden="true"><path d="M3.5 1l3 3-1.6 1.8c.8 2 2.3 3.5 4.3 4.3L11 8.5l3 3-2 2.5C6.5 14 2 9.5 1 3.5z"/></svg>
        +61 (0)7 5550 1497
      </li>
      <li>
        <svg viewBox="0 0 16 16" aria-hidden="true"><path d="M4 1h8v14H4zM5.5 2.5v9.5h5V2.5zM7 13h2v1H7z" fill-rule="evenodd"/></svg>
        +61 (0)400 555 318
      </li>
      <li>
        <svg viewBox="0 0 16 16" aria-hidden="true"><path d="M4 1h8v4H4zM1 6h14v6h-2v-2H3v2H1zM4 11h8v4H4z"/></svg>
        +61 (0)7 5550 1460
      </li>
      <li>
        <svg viewBox="0 0 16 16" aria-hidden="true"><path d="M1 3h14v1L8 9 1 4zM1 5.5l7 5 7-5V13H1z"/></svg>
        mellison@korvalit.com.au
      </li>
      <li>
        <svg viewBox="0 0 16 16" aria-hidden="true"><circle cx="8" cy="8" r="7"/><path d="M4 5c2 0 2 2 4 2s1 3 3 3M9 2c0 2 2 2 3 3" stroke="#f2f2f2" stroke-width="1.3" fill="none"/></svg>
        www.korvalit.com.au
      </li>
    </ul>

    <div class="name-tab"></div>
    <div class="name-band">
      <p class="person-name">MARA ELLISON</p>
      <p class="person-role">Business Development Manager</p>
    </div>
  </section>

  <section class="card card-back" aria-label="Business card back">
    <div class="back-name">Korval</div>
    <ul class="services">
      <li class="service"><span class="service-mark"></span>MapOut</li>
      <li class="service"><span class="service-mark"></span>ShipWell</li>
      <li class="service"><span class="service-mark"></span>KeepSteady</li>
    </ul>
  </section>

</main>
</body>
</html>
```